KLV Plant Services

We are a heavy diesel mechanical business with additional air con certificates, remapping engine rebuilt

Contact Information for Business Card

Company Name, Director Name, Managing Director, Contact details, email and website

Font styles to use
Serif
Script

```html
<!DOCTYPE html>
<html lang="en">
<head>
<meta charset="utf-8">
<title>KLV Plant Services – Business Card</title>
<link href="https://fonts.googleapis.com/css2?family=Arimo:wght@400;700&display=swap" rel="stylesheet">
<style>
  :root {
    --page-bg: #e9e6e1;
    --card-bg: #f3f2f0;
    --card-edge: #c9c7c4;
    --ink-navy: #1d1f4d;
    --ink-text: #2f2f33;
    --ink-black: #141414;
  }
  * { margin: 0; padding: 0; box-sizing: border-box; }
  html, body {
    width: 1170px; height: 1200px; overflow: hidden;
    background: var(--page-bg);
    font-family: "Arimo", Arial, sans-serif;
  }
  .card {
    position: absolute; left: 69px; top: 306px;
    width: 1032px; height: 587px;
    background: var(--card-bg);
    border: 1px solid var(--card-edge);
    border-radius: 22px;
    overflow: hidden;
    box-shadow: 0 18px 40px rgba(0,0,0,0.12);
  }
  .card__crescent { position: absolute; inset: 0; }
  .brand {
    position: absolute; left: 60px; top: 150px;
    display: flex; align-items: center; gap: 16px;
  }
  .brand__dot {
    width: 26px; height: 26px; border-radius: 50%;
    background: var(--ink-navy);
  }
  .brand__name {
    font-size: 44px; font-weight: 700; color: var(--ink-navy);
    letter-spacing: -0.5px;
  }
  .address {
    position: absolute; left: 58px; top: 342px;
    font-size: 25px; line-height: 33px; color: var(--ink-text);
  }
  .contacts {
    position: absolute; left: 58px; top: 432px;
    list-style: none;
    font-size: 25px; line-height: 33px; color: var(--ink-text);
  }
  .contacts li { display: flex; align-items: center; gap: 12px; }
  .contacts svg { width: 22px; height: 22px; fill: var(--ink-navy); }
  .person {
    position: absolute; right: 106px; top: 326px;
    text-align: right;
  }
  .person__name {
    font-size: 37px; font-weight: 700; color: var(--ink-navy); line-height: 44px;
  }
  .person__role { font-size: 24px; color: var(--ink-text); line-height: 30px; }
</style>
</head>
<body>
  <div class="card">
    <svg class="card__crescent" width="1032" height="587" viewBox="0 0 1032 587">
      <defs>
        <mask id="crescent-cut">
          <rect width="1032" height="587" fill="#fff"/>
          <circle cx="715" cy="290" r="280" fill="#000"/>
        </mask>
      </defs>
      <g mask="url(#crescent-cut)" fill="var(--ink-black)">
        <circle cx="745" cy="290" r="290"/>
        <rect x="745" y="0" width="287" height="587"/>
      </g>
    </svg>

    <div class="brand">
      <span class="brand__dot"></span>
      <span class="brand__name">KLV Plant Services</span>
    </div>

    <p class="address">2719 Harborview Lane<br>Glen Oaks, NY 11004</p>

    <ul class="contacts">
      <li>
        <svg viewBox="0 0 24 24" aria-hidden="true"><path d="M6.6 10.8a15.1 15.1 0 0 0 6.6 6.6l2.2-2.2c.3-.3.7-.4 1-.2 1.1.4 2.3.6 3.6.6.6 0 1 .4 1 1V20c0 .6-.4 1-1 1A17 17 0 0 1 3 4c0-.6.4-1 1-1h3.5c.6 0 1 .4 1 1 0 1.3.2 2.5.6 3.6.1.3 0 .7-.2 1z"/></svg>
        (555) 3162-4870
      </li>
      <li>
        <svg viewBox="0 0 24 24" aria-hidden="true"><path d="M2 6h20v12H2z M2 6l10 7 10-7" fill="none" stroke="var(--ink-navy)" stroke-width="0"/><path d="M2 5h20v2l-10 7L2 7z"/><path d="M2 9l10 7 10-7v10H2z"/></svg>
        name@KLV.com
      </li>
      <li>
        <svg viewBox="0 0 24 24" aria-hidden="true"><circle cx="12" cy="12" r="10"/><circle cx="12" cy="12" r="4" fill="var(--card-bg)"/></svg>
        www.KLV.com
      </li>
    </ul>

    <div class="person">
      <p class="person__name">Daniel Harper</p>
      <p class="person__role">Managing Director</p>
    </div>
  </div>
</body>
</html>
```